An internal sign in a physiotherapy clinic with gym. About working hard

We are a physiotherapy clinic / gym and we are wanting an internal wall to be a large sign with a great slogan
We are after 3 parts to it
1. The image / backdrop
2. The slogan
3. Our clinic logo

I have attached some images of the concept of what we are after. It can be climbing a mountain, rockclimbing and even hard work in a gym.

The slogan is:
"IF IT DOESN'T CHALLENGE YOU, IT WON'T CHANGE YOU"

Logo
I have attached a few different versions of our logo to assist you in the sign based on the background

THE SIGN SIZE WILL BE:
2935mm wide x 1885mm high

```html
<!DOCTYPE html>
<html lang="en">
<head>
<meta charset="utf-8">
<title>Northvale Sports Medicine – Wall Sign</title>
<link href="https://fonts.googleapis.com/css2?family=Anton&display=swap" rel="stylesheet">
<style>
  :root {
    --page-bg: #e9ebef;
    --sign-navy: #12174a;
    --sign-navy-light: #2a3585;
    --photo-tone-dark: #3a3f6e;
    --photo-tone-mid: #6a5a58;
    --photo-tone-skin: #a8765a;
    --text-white: #ffffff;
    --text-cyan: #45bfe8;
  }
  * { margin: 0; padding: 0; box-sizing: border-box; }
  html, body {
    width: 1200px;
    height: 900px;
    overflow: hidden;
    background: var(--page-bg);
  }
  .wall-sign {
    position: absolute;
    left: 20px;
    top: 77px;
    width: 1160px;
    height: 745px;
    overflow: hidden;
    background: linear-gradient(100deg, var(--sign-navy) 0%, var(--sign-navy) 45%, var(--sign-navy-light) 100%);
  }
  .hero-photo {
    position: absolute;
    right: 0;
    top: 0;
    width: 42%;
    height: 100%;
  }
  .brand {
    position: absolute;
    left: 181px;
    top: 78px;
    display: flex;
    align-items: center;
    gap: 14px;
    font-family: "Anton", sans-serif;
    color: var(--text-white);
  }
  .brand-dot {
    width: 40px;
    height: 40px;
    border-radius: 50%;
    background: var(--text-cyan);
  }
  .brand-name {
    font-size: 38px;
    line-height: 1;
    letter-spacing: 1px;
  }
  .brand-name span {
    display: block;
    font-size: 20px;
    letter-spacing: 6px;
    margin-top: 6px;
  }
  .slogan {
    position: absolute;
    left: 181px;
    top: 258px;
    font-family: "Anton", sans-serif;
    font-size: 94px;
    line-height: 100px;
    text-transform: uppercase;
    letter-spacing: 0.5px;
  }
  .slogan-line { display: block; white-space: nowrap; }
  .slogan-line--white { color: var(--text-white); }
  .slogan-line--cyan { color: var(--text-cyan); }
</style>
</head>
<body>
  <section class="wall-sign">
    <svg class="hero-photo" role="img" aria-label="Photo of an athlete working hard on an air bike in a gym" viewBox="0 0 100 100" preserveAspectRatio="none">
      <defs>
        <radialGradient id="athleteTone" cx="55%" cy="45%" r="60%">
          <stop offset="0%" stop-color="var(--photo-tone-skin)"/>
          <stop offset="45%" stop-color="var(--photo-tone-mid)"/>
          <stop offset="100%" stop-color="var(--photo-tone-dark)" stop-opacity="0"/>
        </radialGradient>
      </defs>
      <rect width="100" height="100" fill="url(#athleteTone)"/>
    </svg>

    <div class="brand">
      <div class="brand-dot"></div>
      <div class="brand-name">NORTHVALE<span>SPORTS MEDICINE</span></div>
    </div>

    <h1 class="slogan">
      <span class="slogan-line slogan-line--white">If it doesn't</span>
      <span class="slogan-line slogan-line--cyan">challenge you,</span>
      <span class="slogan-line slogan-line--white">it won't</span>
      <span class="slogan-line slogan-line--cyan">change you</span>
    </h1>
  </section>
</body>
</html>
```